Federal IT Consulting Company - Brisolux Consulting Group

We're seeking a skilled web designer to create a modern, bold, and engaging WordPress website for Brisolux Consulting Group, LLC. Our company specializes in federal IT consulting, and our name is a play on "Brightening Solutions." The website should reflect our expertise in the federal technology marketplace and position us as a trusted partner for clients navigating their IT journey.

contact: info@brisoluxgrp-example.com

Current Status

WordPress is already installed on our hosting account
We have an existing logo (may need modernization)

Design Requirements

Style:

Modern and visually striking design
Bold elements to convey confidence and expertise
Incorporate the concept of "brightening solutions" into the design

Features:

Modern UX sliders for dynamic content presentation
Eye-catching, high-quality images (stock photos to be sourced by the designer)
Responsive design for all devices

Color Scheme:

To be proposed by the designer, should align with our brand and convey trust and technological expertise

Logo:

Evaluate our current logo
Create a transparent background version if needed
Propose modernization if deemed necessary

Accessibility:

Ensure design elements are accessible to users with disabilities
Use high contrast ratios for text and background colors
Provide text alternatives for non-text content

Website Structure
Create the following pages, with the possibility of subpages:

Home
Services
About
Contact

Specific Page Requirements
Home Page

Striking hero section with a clear value proposition
Overview of our services
Client testimonials or trust indicators

Services Page

Detailed list of our IT consulting services
Clear explanation of how we help navigate the federal IT landscape

About Page

Company history and mission
Team highlights (if applicable)
Our approach to federal IT consulting

Contact Page

Contact form
Other contact methods (phone, email)

Technical Requirements

Fully responsive design
SEO best practices implemented
Fast loading times
Integration with necessary plugins (to be discussed)
Training on how to update and maintain the site
Full compliance with Web Content Accessibility Guidelines (WCAG) 2.1 Level AA
Adherence to Section 508 standards for federal website accessibility
Implementation of necessary features for ADA compliance
Updates

Designs look the same

Target Market(s)

US Federal Govt customers looking for IT support.

Industry/Entity Type

IT Consulting

Coding

Coded - Design and coding required

Colors
0054AA
0677BA
7BADD7
CADEEF
E8F1F8
0094D4
00A9DD
6FCCEA
C7EBF8
E9F6FB
00AB8E
00BBA5
67D7C9
C6EFE9
E9F9F6

```html
<!DOCTYPE html>
<html lang="en">
<head>
<meta charset="utf-8">
<title>Brisolux Consulting Group</title>
<link rel="stylesheet" href="https://fonts.googleapis.com/css2?family=Poppins:wght@400;500;600;700&display=swap">
<style>
:root{
  --blue:#00A9DD;
  --blue-deep:#0094D4;
  --blue-light:#6FCCEA;
  --blue-pale:#C7EBF8;
  --ink:#333a40;
  --body:#555b60;
  --grey-bg:#eeeeee;
  --white:#ffffff;
}
*{margin:0;padding:0;box-sizing:border-box}
html,body{width:1200px;height:4277px;overflow:hidden}
body{position:relative;font-family:"Poppins",sans-serif;color:var(--ink);background:var(--white)}
.abs{position:absolute}
.center{text-align:center}

/* header */
.site-header{left:0;top:0;width:1200px;height:126px;background:var(--white)}
.brand{display:flex;align-items:center;gap:10px;font-weight:700;color:var(--ink);letter-spacing:2px}
.brand-dot{width:40px;height:40px;border-radius:50%;border:5px solid var(--blue)}
.header-brand{left:75px;top:38px;font-size:34px}
.main-nav{top:52px;left:620px;display:flex;gap:32px;font-size:13px;color:var(--ink)}
.main-nav a{color:inherit;text-decoration:none}
.main-nav .active{color:var(--blue);border-bottom:2px solid var(--blue);padding-bottom:10px}
.nav-cta{left:1009px;top:46px;width:115px;height:34px;border-radius:17px;background:var(--blue);color:var(--white);font-size:13px;display:flex;align-items:center;justify-content:center}

/* hero */
.hero{left:0;top:126px;width:1200px;height:774px;background:var(--grey-bg)}
.hero-photo{left:600px;top:126px;width:600px;height:774px;background:linear-gradient(160deg,#dfe6ea 0%,#b9c2c8 55%,#8f989e 100%);border-top-left-radius:300px}
.hero-title{left:72px;top:272px;font-size:88px;font-weight:700;letter-spacing:6px;color:var(--ink);line-height:1}
.hero-tagline{left:75px;top:370px;width:520px;font-size:17px;font-weight:500;color:var(--blue-deep);line-height:25px}
.btn-outline{display:flex;align-items:center;justify-content:center;gap:12px;border:2px solid var(--blue);border-radius:30px;font-size:16px;font-weight:500;color:var(--ink);background:transparent}
.btn-icon{width:22px;height:22px}
.hero-btn{left:73px;top:463px;width:186px;height:53px}

/* feature card */
.feature-card{left:95px;top:807px;width:1010px;height:247px;background:var(--white);box-shadow:0 6px 24px rgba(0,0,0,.14);display:flex}
.feature{flex:1;display:flex;flex-direction:column;align-items:center;padding-top:36px;position:relative}
.feature+.feature::before{content:"";position:absolute;left:0;top:28px;height:180px;border-left:1.5px solid #b8bcc0}
.feature-icon{width:102px;height:102px;border-radius:50%;border:2px solid var(--blue);display:flex;align-items:center;justify-content:center}
.feature-icon span{width:88px;height:88px;border-radius:50%;background:var(--blue);display:block}
.feature h3{margin-top:30px;font-size:16px;font-weight:600;text-align:center;line-height:20px;color:var(--ink)}

/* section titles */
.section-title{left:0;width:1200px;text-align:center;font-size:44px;font-weight:600;color:var(--ink)}
.section-sub{left:0;width:1200px;display:flex;justify-content:center;align-items:center;gap:12px;font-size:23px;font-weight:600;letter-spacing:3px;color:var(--blue)}
.section-sub i{display:block;height:3px;background:var(--blue)}

/* services */
.service{width:300px;text-align:center}
.service-icon{width:110px;height:110px;margin:0 auto;border-radius:50%;background:radial-gradient(circle,var(--blue-pale) 0 45%,var(--blue) 46% 100%)}
.service h3{margin-top:28px;font-size:17px;font-weight:600;color:var(--ink)}
.service p{margin-top:12px;font-size:13px;line-height:23px;color:var(--body)}
.service-highlight{left:461px;top:1353px;width:276px;height:274px;border:2px solid var(--blue);border-radius:22px}
.service-more{left:588px;top:1587px;width:22px;height:22px}

/* about */
.about-ring{left:121px;top:2058px;width:438px;height:438px;border-radius:50%;border:2px solid var(--blue)}
.about-photo{left:140px;top:2076px;width:400px;height:400px;border-radius:50%;background:linear-gradient(135deg,#e9edf0 0%,#aeb6bd 50%,#4b5560 100%)}
.about-dot{left:461px;top:2478px;width:60px;height:60px;border-radius:50%;background:var(--blue)}
.about-title{left:638px;top:2098px;font-size:44px;font-weight:600;color:var(--ink)}
.about-sub{left:638px;top:2151px;display:flex;align-items:center;gap:12px;font-size:22px;font-weight:600;letter-spacing:3px;color:var(--blue)}
.about-sub i{display:block;width:46px;height:3px;background:var(--blue)}
.about-text{left:641px;top:2231px;width:440px;font-size:13px;line-height:23px;color:var(--body)}
.about-btn{left:644px;top:2369px;width:186px;height:53px}

/* call to action band */
.cta-band{left:0;top:2663px;width:1200px;height:380px;background:linear-gradient(120deg,#0a8fd0 0%,var(--blue) 50%,#1fb4e6 100%)}
.cta-title{left:0;top:2728px;width:1200px;text-align:center;font-size:40px;font-weight:500;line-height:54px;color:var(--white)}
.cta-title strong{font-weight:600}
.cta-text{left:0;top:2860px;width:1200px;text-align:center;font-size:13px;line-height:23px;color:var(--white)}
.cta-btn{left:506px;top:2928px;width:186px;height:53px;border-color:var(--white);color:var(--white)}

/* testimonials */
.lead{left:0;width:1200px;text-align:center;font-size:13px;line-height:23px;color:var(--body)}
.testimonial{width:375px;height:193px;background:var(--white);box-shadow:0 4px 20px rgba(0,0,0,.12);text-align:center}
.testimonial .avatar{position:absolute;left:152px;top:-39px;width:72px;height:72px;border-radius:50%;border:2px solid var(--blue);background:var(--blue-pale)}
.testimonial .name{position:absolute;left:0;top:44px;width:375px;font-size:13px;font-weight:600;font-style:italic;color:var(--blue)}
.testimonial .role{position:absolute;left:0;top:64px;width:375px;font-size:9px;color:var(--body)}
.testimonial .quote-mark{position:absolute;right:18px;top:-6px;font-size:96px;font-weight:700;color:#dcdfe2;line-height:1}
.testimonial p{position:absolute;left:40px;top:94px;width:295px;font-size:13px;line-height:22px;color:var(--body)}
.testimonial .bar{position:absolute;left:30px;bottom:0;width:316px;height:5px;background:var(--blue)}
.slider-arrow{width:40px;height:40px;border-radius:50%;display:flex;align-items:center;justify-content:center;background:var(--white)}
.slider-prev{left:114px;top:3544px;box-shadow:0 2px 8px rgba(0,0,0,.18)}
.slider-next{left:1057px;top:3544px;border:1.5px solid var(--blue)}
.dots{left:575px;top:3741px;display:flex;gap:13px}
.dots i{display:block;width:12px;height:12px;border-radius:50%;background:var(--blue-pale)}
.dots i.on{background:var(--blue)}

/* footer */
.site-footer{left:0;top:3863px;width:1200px;height:414px;background:var(--blue)}
.footer-brand{left:78px;top:4020px;font-size:34px;color:var(--white)}
.footer-brand .brand-dot{border-color:var(--white)}
.social{left:124px;top:4124px;display:flex;gap:10px}
.social span{width:30px;height:30px;border:1.5px solid var(--white);border-radius:4px;display:block}
.footer-col h4{font-size:16px;font-weight:500;color:var(--white)}
.footer-col h4::after{content:"";display:block;width:36px;height:2px;background:var(--white);margin-top:10px}
.quick-links{left:402px;top:3952px}
.quick-links ul{list-style:none;margin-top:24px}
.quick-links li{font-size:13px;color:var(--white);line-height:27px;display:flex;align-items:center;gap:4px}
.quick-links li::before{content:"";width:12px;height:12px;border:1.5px solid var(--white);border-radius:50%}
.contact-col{left:609px;top:3952px}
.contact-row{display:flex;gap:18px;align-items:center;margin-top:22px;color:var(--white);font-size:12px;line-height:16px}
.contact-row:first-of-type{margin-top:24px}
.contact-row svg{width:26px;height:26px;flex:none}
.contact-row small{display:block;font-size:11px}
.newsletter{left:900px;top:3952px;width:230px}
.newsletter p{margin-top:22px;font-size:13px;line-height:17px;color:var(--white)}
.newsletter-field{margin-top:18px;margin-left:-7px;width:209px;height:35px;border:1.5px solid var(--white);border-radius:18px;display:flex;align-items:center;justify-content:space-between;padding:0 6px 0 16px;font-size:11px;color:var(--blue-pale)}
.footer-rule{left:75px;top:4190px;width:1049px;height:2px;background:var(--white)}
.copyright{left:0;top:4228px;width:1200px;text-align:center;font-size:11px;color:var(--white)}
</style>
</head>
<body>

<header class="abs site-header">
  <div class="abs brand header-brand"><span class="brand-dot"></span>BRISOLUX</div>
  <nav class="abs main-nav">
    <a class="active" href="#">HOME</a><a href="#">SERVICES</a><a href="#">ABOUT US</a><a href="#">TESTIMONIALS</a>
  </nav>
  <a class="abs nav-cta">CONTACT US</a>
</header>

<section class="abs hero" aria-label="Hero"></section>
<div class="abs hero-photo" role="img" aria-label="Smiling consultant in a grey blazer holding an open laptop"></div>
<h1 class="abs hero-title">BRISOLUX</h1>
<p class="abs hero-tagline">We provide customized solutions to help you achieve your business goals and stay ahead of the competitions</p>
<a class="abs btn-outline hero-btn">CONTACT US
  <svg class="btn-icon" viewBox="0 0 24 24" fill="none" stroke="#00A9DD" stroke-width="2.4"><circle cx="12" cy="12" r="9"/><path d="M10 8l4 4-4 4"/></svg></a>

<div class="abs feature-card">
  <div class="feature"><div class="feature-icon" role="img" aria-label="Responsive devices icon"><span></span></div><h3>RESPONSIVE DESIGN<br>AND SECURITY</h3></div>
  <div class="feature"><div class="feature-icon" role="img" aria-label="Light bulb icon"><span></span></div><h3>INNOVATION AN<br>TECHNOLOGY</h3></div>
  <div class="feature"><div class="feature-icon" role="img" aria-label="Network icon"><span></span></div><h3>VERSATILITY IN<br>SERVICES</h3></div>
  <div class="feature"><div class="feature-icon" role="img" aria-label="Product package icon"><span></span></div><h3>EXPANDED<br>PRODUCT LINE</h3></div>
</div>

<h2 class="abs section-title" style="top:1192px">OUR SERVICES</h2>
<div class="abs section-sub" style="top:1248px"><i style="width:52px"></i>WHAT WE DO<i style="width:52px"></i></div>

<div class="abs service-highlight"></div>
<div class="abs service" style="left:112px;top:1369px"><div class="service-icon" role="img" aria-label="Application design icon"></div><h3>APPLICATION DESIGN</h3><p>Lorem ipsum dolor sit amet, conse<br>ctetur adipiscing elit,</p></div>
<div class="abs service" style="left:449px;top:1369px"><div class="service-icon" role="img" aria-label="Web hosting icon"></div><h3>WEB HOSTING</h3><p>Lorem ipsum dolor sit amet, conse<br>ctetur adipiscing elit,</p></div>
<div class="abs service" style="left:781px;top:1369px"><div class="service-icon" role="img" aria-label="Data science icon"></div><h3>DATA SCIENCE</h3><p>Lorem ipsum dolor sit amet, conse<br>ctetur adipiscing elit,</p></div>
<svg class="abs service-more" viewBox="0 0 24 24" fill="none" stroke="#00A9DD" stroke-width="2.4"><circle cx="12" cy="12" r="9"/><path d="M10 8l4 4-4 4"/></svg>
<div class="abs service" style="left:112px;top:1665px"><div class="service-icon" role="img" aria-label="SEO optimization icon"></div><h3>SEO OPTIMIZATION</h3><p>Lorem ipsum dolor sit amet, conse<br>ctetur adipiscing elit,</p></div>
<div class="abs service" style="left:449px;top:1665px"><div class="service-icon" role="img" aria-label="Digital marketing icon"></div><h3>DIGITAL MARKETING</h3><p>Lorem ipsum dolor sit amet, conse<br>ctetur adipiscing elit</p></div>
<div class="abs service" style="left:781px;top:1665px"><div class="service-icon" role="img" aria-label="Data security icon"></div><h3>DATA SECURITY</h3><p>Lorem ipsum dolor sit amet, conse<br>ctetur adipiscing elit</p></div>

<div class="abs about-ring"></div>
<div class="abs about-photo" role="img" aria-label="Business team meeting around a laptop and tablet in an office"></div>
<div class="abs about-dot"></div>
<h2 class="abs about-title">ABOUT US</h2>
<div class="abs about-sub">WHO WE ARE<i></i></div>
<p class="abs about-text">Lorem ipsum dolor sit amet, conse ctetur adipiscing elit, sed do eiusmod tempor&nbsp; incididunt ut labore et dolore magna aliqua. Ut enim ad minim veniam, quis nostrud exercitation ullamco laboris nisi ut aliquip ex ea commodo consequat</p>
<a class="abs btn-outline about-btn">KNOW MORE
  <svg class="btn-icon" viewBox="0 0 24 24" fill="none" stroke="#00A9DD" stroke-width="2.4"><circle cx="12" cy="12" r="9"/><path d="M10 8l4 4-4 4"/></svg></a>

<section class="abs cta-band" aria-label="Call to action"></section>
<h2 class="abs cta-title">DIGITALLY TRANSFORM &amp; GROW YOUR BUSINESS<br><strong>WANT TO WORK WITH US?</strong></h2>
<p class="abs cta-text">Lorem ipsum dolor sit amet, conse ctetur adipiscing elit, sed do eiusmod tempor&nbsp; incididunt ut labore et dolore magna aliqua.<br>Ut enim ad minim veniam, quis nostrud exercitation ullamco laboris nisi ut aliquip ex ea commodo consequat</p>
<a class="abs btn-outline cta-btn">CONTACT US
  <svg class="btn-icon" viewBox="0 0 24 24" fill="none" stroke="#ffffff" stroke-width="2.4"><circle cx="12" cy="12" r="9"/><path d="M10 8l4 4-4 4"/></svg></a>

<h2 class="abs section-title" style="top:3206px">CLIENT TESTIMONIALS</h2>
<div class="abs section-sub" style="top:3267px"><i style="width:135px"></i>HAPPY CLIENTS<i style="width:128px"></i></div>
<p class="abs lead" style="top:3325px">Lorem ipsum dolor sit amet, conse ctetur adipiscing elit, sed do&nbsp; eiusmod tempor&nbsp; incididunt ut labore et dolore magna aliqua.<br>Ut enim ad minim veniam, quis nostrud exercitation ullamco laboris nisi ut aliquip ex ea commodo consequat</p>

<div class="abs slider-arrow slider-prev"><svg width="12" height="12" viewBox="0 0 12 12" fill="none" stroke="#333a40" stroke-width="1.8"><path d="M8 2L4 6l4 4"/></svg></div>
<article class="abs testimonial" style="left:203px;top:3469px">
  <div class="avatar" role="img" aria-label="Client portrait"></div>
  <span class="quote-mark">&#8220;</span>
  <div class="name">Daniel Whitford</div><div class="role">Managing Director</div>
  <p>Lorem ipsum dolor sit amet, conse ctetuer adipiscing elit. Aenean comodo ligula eget dolorenean massa.</p>
  <div class="bar"></div>
</article>
<article class="abs testimonial" style="left:631px;top:3469px">
  <div class="avatar" role="img" aria-label="Client portrait"></div>
  <span class="quote-mark">&#8220;</span>
  <div class="name">Daniel Whitford</div><div class="role">Managing Director</div>
  <p>Lorem ipsum dolor sit amet, conse ctetuer adipiscing elit. Aenean comodo ligula eget dolorenean massa.</p>
  <div class="bar"></div>
</article>
<div class="abs slider-arrow slider-next"><svg width="12" height="12" viewBox="0 0 12 12" fill="none" stroke="#00A9DD" stroke-width="1.8"><path d="M4 2l4 4-4 4"/></svg></div>
<div class="abs dots"><i></i><i></i><i class="on"></i></div>

<footer class="abs site-footer"></footer>
<div class="abs brand footer-brand"><span class="brand-dot"></span>BRISOLUX</div>
<div class="abs social" aria-label="Social links"><span></span><span></span><span></span><span></span></div>

<div class="abs footer-col quick-links">
  <h4>QUICK LINKS</h4>
  <ul><li>Home</li><li>Services</li><li>About</li><li>Blog</li><li>Contact Us</li></ul>
</div>

<div class="abs footer-col contact-col">
  <h4>CONTACT US</h4>
  <div class="contact-row">
    <svg viewBox="0 0 26 26" fill="none" stroke="#fff" stroke-width="1.4"><rect x="1" y="1" width="24" height="24" rx="3"/><path d="M9 8c0 5 4 9 9 9l1-2-2-1.5-1.5 1c-1.6-.8-2.7-1.9-3.5-3.5l1-1.5L11.5 7z"/></svg>
    <div><small>CALL US</small>8012 555 0147</div>
  </div>
  <div class="contact-row">
    <svg viewBox="0 0 26 26" fill="none" stroke="#fff" stroke-width="1.4"><rect x="1" y="1" width="24" height="24" rx="3"/><rect x="7" y="9" width="12" height="8" fill="#fff"/><path d="M7 9l6 4 6-4" stroke="#00A9DD"/></svg>
    <div><small>EMAIL US</small>info@brisoluxgrp-example.com</div>
  </div>
  <div class="contact-row">
    <svg viewBox="0 0 26 26" fill="none" stroke="#fff" stroke-width="1.4"><rect x="1" y="1" width="24" height="24" rx="3"/><path d="M13 20s-5-5-5-8.5a5 5 0 0110 0C18 15 13 20 13 20z"/><circle cx="13" cy="11.5" r="1.6"/></svg>
    <div>Address line Dummy Here<br>Address line Here</div>
  </div>
</div>

<div class="abs footer-col newsletter">
  <h4>OUR NEWSLETTER</h4>
  <p>Subscribe our newsletter to get the latest news.</p>
  <div class="newsletter-field">Enter Email Address
    <svg width="24" height="24" viewBox="0 0 24 24" fill="none" stroke="#fff" stroke-width="1.5"><circle cx="12" cy="12" r="10.5"/><path d="M7 12h10M13 8l4 4-4 4"/></svg>
  </div>
</div>

<div class="abs footer-rule"></div>
<p class="abs copyright">Copyright © 2024 All Rights Reserved By Company name</p>

</body>
</html>
```